7K packaging design

We are a wholesaler for Automotive Spare Parts in Jordan and Iraq market and we needs to import spare parts from China under our company private brand "7K"
The 7K brand’s product lines include Filtration, Braking Systems, Wheels, Wheel Bolts & Nuts, Shock Absorbers, Sensors, Cooling Systems, Axles and more.
The aim of the project is to unify the brand packaging across all the product lines , we will start by the brake pads then based on the approved design we will do the other products

Target Market(s)

Jordan , Iraq Market

Industry/Entity Type

Automotive spare parts

Requirements
Must have
• Name of the product :Ceramic brake pads specs : Superior stopping power Noise suppression Low Dust Technology Made in china
Nice to have
• Brake pad outline image on the box
Should not have
• Blue color

```html
<!DOCTYPE html>
<html lang="en">
<head>
<meta charset="utf-8">
<title>7K packaging design</title>
<link rel="stylesheet" href="https://fonts.googleapis.com/css2?family=Oswald:wght@600&family=Archivo:wght@700;900&display=swap">
<style>
  :root {
    --bg: #ebebeb;
    --red: #d0131c;
    --red-bright: #e41b23;
    --red-deep: #a90d15;
    --red-dark: #6b0a10;
    --black-red: #1c0d0e;
    --white: #ffffff;
    --pad-grey: #4a4849;
    --tab: #3a3a3c;
  }
  * { margin: 0; padding: 0; box-sizing: border-box; }
  html, body { width: 1200px; height: 789px; overflow: hidden; background: var(--bg); }
  .canvas { position: relative; width: 1200px; height: 789px; }

  .panel { position: absolute; overflow: hidden; }

  /* shared pieces */
  .brand-mark { position: absolute; display: flex; align-items: center; }
  .brand-dot { border-radius: 50%; background: var(--white); flex: none; }
  .brand-name { font-family: "Oswald", sans-serif; font-weight: 600; color: var(--white); line-height: 1; }
  .feature-list { position: absolute; list-style: none; font-family: "Archivo", sans-serif; font-weight: 700; color: var(--white); line-height: 1.15; }
  .feature { display: flex; align-items: center; }
  .feature svg { flex: none; }
  .origin-tab { position: absolute; bottom: 0; background: var(--tab); border-radius: 7px 7px 0 0; font-family: "Archivo", sans-serif; font-weight: 700; color: var(--white); white-space: nowrap; }
  .car-visual { position: absolute; background: radial-gradient(ellipse at 60% 60%, rgba(210,24,32,.55), rgba(70,8,12,.25) 65%, transparent 80%); }

  /* top panel */
  .box-top {
    left: 200px; top: 170px; width: 970px; height: 170px;
    background: linear-gradient(90deg, var(--red-deep) 0%, var(--red-dark) 30%, var(--red-deep) 55%, var(--red) 100%);
  }
  .box-top .car-visual { left: 280px; top: 0; width: 300px; height: 170px; }
  .box-top .brand-mark { left: 110px; top: 52px; gap: 12px; }
  .box-top .brand-dot { width: 22px; height: 22px; }
  .box-top .brand-name { font-size: 66px; }
  .top-title {
    position: absolute; right: 190px; top: 18px;
    font-family: "Archivo", sans-serif; font-weight: 900; font-size: 26px;
    color: var(--white); letter-spacing: 1.5px; line-height: 1;
  }
  .top-stripes { position: absolute; left: 440px; top: 54px; }
  .pad-outline {
    position: absolute; left: 520px; top: 58px; width: 260px; height: 90px;
    border-radius: 30px 50px 40px 30px;
    background: linear-gradient(180deg, rgba(255,255,255,.14), rgba(255,255,255,.04));
  }
  .box-top .feature-list { left: 810px; top: 22px; font-size: 8px; }
  .box-top .feature { gap: 7px; height: 26px; }
  .box-top .feature svg { width: 17px; height: 17px; }
  .box-top .origin-tab { left: 800px; padding: 3px 10px 2px; font-size: 6px; }

  /* front panel */
  .box-front {
    left: 200px; top: 340px; width: 970px; height: 270px;
    background: linear-gradient(90deg, var(--black-red) 0%, var(--red-dark) 30%, var(--red-deep) 50%, var(--red) 100%);
    box-shadow: 0 18px 30px rgba(0,0,0,.16);
  }
  .box-front .car-visual { left: 180px; top: 0; width: 340px; height: 270px; }
  .title-band {
    position: absolute; left: 390px; top: 14px; width: 580px; height: 74px;
    background: linear-gradient(90deg, var(--red-bright), var(--red));
    clip-path: polygon(8% 0, 100% 0, 100% 100%, 0 100%);
  }
  .speed-stripes { position: absolute; left: 390px; top: 92px; }
  .product-title {
    position: absolute; left: 480px; top: 20px;
    font-family: "Oswald", sans-serif; font-weight: 600; font-size: 50px;
    color: var(--white); letter-spacing: .5px; transform: skewX(-10deg); line-height: 1;
    white-space: nowrap;
  }
  .box-front .brand-mark { left: 70px; top: 88px; gap: 14px; }
  .box-front .brand-dot { width: 28px; height: 28px; }
  .box-front .brand-name { font-size: 92px; }
  .pad-visual {
    position: absolute; left: 505px; top: 106px; width: 290px; height: 130px;
    border-radius: 26px 50px 26px 20px;
    background: linear-gradient(160deg, #5d5a5b, var(--pad-grey) 60%, #2f2d2e);
  }
  .box-front .feature-list { left: 818px; top: 108px; font-size: 10px; }
  .box-front .feature { gap: 8px; height: 38px; }
  .box-front .feature svg { width: 22px; height: 22px; }
  .box-front .origin-tab { left: 820px; padding: 4px 12px 3px; font-size: 8px; }

  /* end panel */
  .box-end {
    left: 30px; top: 340px; width: 170px; height: 270px;
    background: linear-gradient(180deg, var(--red-deep) 0%, var(--red-dark) 45%, var(--black-red) 100%);
  }
  .box-end .brand-mark { left: 36px; top: 40px; gap: 8px; }
  .box-end .brand-dot { width: 16px; height: 16px; }
  .box-end .brand-name { font-size: 56px; }
  .end-band {
    position: absolute; left: 0; top: 150px; width: 170px; height: 48px;
    background: var(--red); display: flex; align-items: center; justify-content: center;
  }
  .end-title {
    font-family: "Oswald", sans-serif; font-weight: 600; font-size: 17px;
    color: var(--white); letter-spacing: .5px; white-space: nowrap;
  }
</style>
</head>
<body>
<main class="canvas">

  <section class="panel box-top">
    <div class="car-visual" role="img" aria-label="Red-tinted photo of a car wheel"></div>
    <div class="brand-mark">
      <span class="brand-dot"></span>
      <span class="brand-name">7K</span>
    </div>
    <svg class="top-stripes" width="70" height="24" viewBox="0 0 70 24">
      <g fill="#ffffff" opacity=".85">
        <polygon points="8,0 16,0 8,24 0,24"/>
        <polygon points="24,0 32,0 24,24 16,24"/>
        <polygon points="40,0 48,0 40,24 32,24"/>
        <polygon points="56,0 64,0 56,24 48,24"/>
      </g>
    </svg>
    <h2 class="top-title">CERAMIC BRAKE PADS</h2>
    <div class="pad-outline" role="img" aria-label="White line drawing of a brake pad outline"></div>
    <ul class="feature-list">
      <li class="feature">
        <svg viewBox="0 0 24 24" fill="none" stroke="#fff" stroke-width="2"><circle cx="12" cy="12" r="10"/><circle cx="12" cy="12" r="4"/></svg>
        <span>SUPERIOR<br>STOPPING POWER</span>
      </li>
      <li class="feature">
        <svg viewBox="0 0 24 24" fill="none" stroke="#fff" stroke-width="2"><path d="M3 9h4l5-4v14l-5-4H3z"/><path d="M16 8l4-2M16 12h5M16 16l4 2"/></svg>
        <span>NOISE<br>SUPPRESSION</span>
      </li>
      <li class="feature">
        <svg viewBox="0 0 24 24" fill="#fff"><circle cx="6" cy="7" r="2"/><circle cx="14" cy="5" r="1.5"/><circle cx="18" cy="11" r="2"/><circle cx="9" cy="14" r="1.5"/><circle cx="15" cy="18" r="2"/><circle cx="5" cy="19" r="1.5"/></svg>
        <span>LOW DUST<br>TECHNOLOGY</span>
      </li>
    </ul>
    <div class="origin-tab">MADE IN CHINA</div>
  </section>

  <section class="panel box-end">
    <div class="brand-mark">
      <span class="brand-dot"></span>
      <span class="brand-name">7K</span>
    </div>
    <div class="end-band"><span class="end-title">CERAMIC BRAKE PADS</span></div>
  </section>

  <section class="panel box-front">
    <div class="car-visual" role="img" aria-label="Red-tinted photo of a car side profile and wheel"></div>
    <div class="title-band"></div>
    <svg class="speed-stripes" width="100" height="36" viewBox="0 0 100 36">
      <g fill="#ffffff">
        <polygon points="12,0 22,0 12,36 2,36"/>
        <polygon points="34,0 44,0 34,36 24,36"/>
        <polygon points="56,0 66,0 56,36 46,36"/>
        <polygon points="78,0 88,0 78,36 68,36"/>
      </g>
    </svg>
    <h1 class="product-title">CERAMIC BRAKE PADS</h1>
    <div class="brand-mark">
      <span class="brand-dot"></span>
      <span class="brand-name">7K</span>
    </div>
    <div class="pad-visual" role="img" aria-label="Photo of a pair of ceramic brake pads"></div>
    <ul class="feature-list">
      <li class="feature">
        <svg viewBox="0 0 24 24" fill="none" stroke="#fff" stroke-width="2"><circle cx="12" cy="12" r="10"/><circle cx="12" cy="12" r="4"/></svg>
        <span>SUPERIOR<br>STOPPING<br>POWER</span>
      </li>
      <li class="feature">
        <svg viewBox="0 0 24 24" fill="none" stroke="#fff" stroke-width="2"><path d="M3 9h4l5-4v14l-5-4H3z"/><path d="M16 8l4-2M16 12h5M16 16l4 2"/></svg>
        <span>NOISE<br>SUPPRESSION</span>
      </li>
      <li class="feature">
        <svg viewBox="0 0 24 24" fill="#fff"><circle cx="6" cy="7" r="2"/><circle cx="14" cy="5" r="1.5"/><circle cx="18" cy="11" r="2"/><circle cx="9" cy="14" r="1.5"/><circle cx="15" cy="18" r="2"/><circle cx="5" cy="19" r="1.5"/></svg>
        <span>LOW DUST<br>TECHNOLOGY</span>
      </li>
    </ul>
    <div class="origin-tab">MADE IN CHINA</div>
  </section>

</main>
</body>
</html>
```